Walk Beside The River

Business Card design

Target Market(s)

People who require support in the commnity

Industry/Entity Type

Mental Health Support

Contact Information for Business Card

Mental Health Support Rosalind Tavener walkbesidetheriver@mailcove.com.au 0481 637 092 PO Box 926 Tallowridge QLD 4571

Colors
6B429C
8869AF
B7A5CE
E3DAEB
F3F0F8

Requirements
Must have
• Logo & details listed above
Should not have
• No red or orange

```html
<!DOCTYPE html>
<html lang="en">
<head>
<meta charset="utf-8">
<title>Walk Beside The River — Business Card</title>
<link rel="stylesheet" href="https://fonts.googleapis.com/css2?family=Lato:wght@400;900&display=swap">
<style>
  :root {
    --purple: #6B429C;
    --lilac: #B7A5CE;
    --mist: #F3F0F8;
    --sun: #F7EC2A;
    --cream: #FBF6E4;
    --white: #ffffff;
    --backdrop: #2b2b2d;
  }
  * { margin: 0; padding: 0; box-sizing: border-box; }
  html, body { width: 1200px; height: 875px; overflow: hidden; }
  body {
    background: var(--backdrop);
    font-family: "Lato", sans-serif;
    display: flex;
    flex-direction: column;
    align-items: center;
    justify-content: center;
    gap: 40px;
  }
  .card {
    width: 630px;
    height: 360px;
    border-radius: 22px;
    position: relative;
    overflow: hidden;
  }
  .card--front {
    background: var(--purple);
    display: flex;
    align-items: center;
    justify-content: center;
    gap: 18px;
  }
  .front-mark {
    width: 34px; height: 34px;
    border-radius: 50%;
    background: var(--sun);
  }
  .front-name {
    color: var(--cream);
    font-weight: 900;
    font-size: 30px;
    letter-spacing: 0.14em;
    text-transform: uppercase;
  }
  .card--back { background: var(--white); }
  .back-badge {
    position: absolute;
    top: 26px; right: 34px;
    width: 134px; height: 134px;
    border-radius: 50%;
    background: var(--purple);
    display: flex;
    align-items: center;
    justify-content: center;
    text-align: center;
    padding: 18px;
  }
  .back-badge-name {
    color: var(--cream);
    font-weight: 900;
    font-size: 13px;
    letter-spacing: 0.12em;
    line-height: 1.35;
    text-transform: uppercase;
  }
  .divider {
    position: absolute;
    left: 36px; right: 58px;
    top: 248px;
    height: 2px;
    background: var(--purple);
  }
  .person {
    position: absolute;
    left: 36px; top: 178px;
    color: var(--purple);
  }
  .person-name {
    font-weight: 900;
    font-size: 34px;
    letter-spacing: -0.01em;
    text-transform: uppercase;
    line-height: 1;
  }
  .person-role { font-size: 19px; margin-top: 6px; }
  .contact {
    position: absolute;
    left: 40px; top: 262px;
    color: var(--purple);
    list-style: none;
  }
  .contact li { display: flex; align-items: center; gap: 10px; }
  .contact-phone { font-size: 25px; }
  .contact-email { font-size: 17px; margin-top: 4px; }
  .contact svg { flex: none; }
  .address {
    position: absolute;
    right: 58px; top: 186px;
    color: var(--purple);
    font-size: 18px;
    font-style: normal;
    text-align: right;
    line-height: 1.35;
  }
</style>
</head>
<body>
  <section class="card card--front" aria-label="Card front">
    <span class="front-mark"></span>
    <span class="front-name">Walk Beside The River</span>
  </section>

  <section class="card card--back" aria-label="Card back">
    <div class="back-badge"><span class="back-badge-name">Walk Beside The River</span></div>

    <div class="person">
      <p class="person-name">Rosalind Tavener</p>
      <p class="person-role">Mental Health Support</p>
    </div>

    <address class="address">PO Box 926<br>Tallowridge QLD 4571</address>

    <div class="divider"></div>

    <ul class="contact">
      <li class="contact-phone">
        <svg width="18" height="18" viewBox="0 0 24 24" aria-hidden="true">
          <path fill="var(--purple)" d="M6.6 10.8a15.1 15.1 0 0 0 6.6 6.6l2.2-2.2a1 1 0 0 1 1-.25 11.4 11.4 0 0 0 3.6.57 1 1 0 0 1 1 1V20a1 1 0 0 1-1 1A17 17 0 0 1 3 4a1 1 0 0 1 1-1h3.5a1 1 0 0 1 1 1c0 1.25.2 2.450.57 3.6a1 1 0 0 1-.25 1z"/>
        </svg>
        0481 637 092
      </li>
      <li class="contact-email">
        <svg width="18" height="14" viewBox="0 0 24 18" aria-hidden="true">
          <rect x="0" y="0" width="24" height="18" rx="2" fill="var(--purple)"/>
          <path d="M1 2l11 8 11-8" stroke="var(--white)" stroke-width="2" fill="none"/>
        </svg>
        walkbesidetheriver@mailcove.com.au
      </li>
    </ul>
  </section>
</body>
</html>
```